Coastline Premier Retreats Business Card Design

Design a business card for Coastline Premier Retreats. Look at the website for colors and reference. Card should have logo, name, title, office number, mobile number, email, URL and a tagline like, "Luxury Hotel & Resort Email Marketing" (This might change).

https://www.coastlinepremierretreats.example

The rest I will leave up to your imagination.

Contact Information for Business Card

Logo, name, title, office number, mobile number, email, URL and a tagline like, "Luxury Hotel & Resort Email Marketing" (This might change).

```html
<!DOCTYPE html>
<html lang="en">
<head>
<meta charset="utf-8">
<title>Coastline Premier Retreats – Business Card</title>
<link rel="stylesheet" href="https://fonts.googleapis.com/css2?family=Open+Sans:wght@400;600;700&display=swap">
<style>
  :root {
    --page-bg: #d8cdbf;
    --card-bg: #e2d4bf;
    --card-edge: #efe6da;
    --brand-orange: #d4621f;
    --band-orange: #cf6a2c;
    --tagline: #eea97c;
    --ink: #151515;
  }
  * { margin: 0; padding: 0; box-sizing: border-box; }
  html, body {
    width: 1200px; height: 1046px; overflow: hidden;
    background: var(--page-bg);
    font-family: "Open Sans", Arial, sans-serif;
  }
  .business-card {
    position: absolute; left: 60px; top: 228px;
    width: 1080px; height: 590px;
    background: var(--card-bg);
    border: 1px solid var(--card-edge);
  }
  .tagline-band {
    position: absolute; left: 0; top: 0;
    width: 139px; height: 100%;
    background: var(--band-orange);
    display: flex; align-items: center; justify-content: center;
  }
  .tagline {
    writing-mode: vertical-rl; transform: rotate(180deg);
    color: var(--tagline);
    font-size: 25px; line-height: 33px; font-weight: 400;
    text-align: left;
  }
  .brand {
    position: absolute; right: 42px; top: 50px;
    display: flex; align-items: center; gap: 16px;
  }
  .brand-mark { width: 22px; height: 22px; background: var(--brand-orange); }
  .brand-name {
    color: var(--ink); font-weight: 700; text-transform: uppercase;
    text-align: right; line-height: 1.05;
  }
  .brand-name .line-main { display: block; font-size: 50px; letter-spacing: 1px; }
  .brand-name .line-sub { display: block; font-size: 21px; letter-spacing: 4px; }
  .person {
    position: absolute; right: 90px; top: 264px; text-align: right;
  }
  .person-name { font-size: 47px; font-weight: 700; color: var(--ink); line-height: 1.2; }
  .person-name .first { color: var(--brand-orange); }
  .person-title { font-size: 24px; font-weight: 600; color: var(--ink); margin-top: 2px; }
  .accent-bar {
    position: absolute; left: 1051px; top: 268px;
    width: 27px; height: 82px; background: var(--brand-orange);
  }
  .contacts {
    position: absolute; right: 39px; top: 410px;
    list-style: none;
  }
  .contacts li {
    display: flex; align-items: center; justify-content: flex-end;
    height: 35.5px; font-size: 25px; color: var(--ink); letter-spacing: 0.3px;
  }
  .contacts svg { width: 22px; height: 22px; margin-left: 20px; flex: none; }
</style>
</head>
<body>
  <article class="business-card">
    <aside class="tagline-band">
      <p class="tagline">Luxury Hotel &amp;<br>Resort Email Marketing</p>
    </aside>

    <header class="brand">
      <span class="brand-mark"></span>
      <span class="brand-name">
        <span class="line-main">Coastline</span>
        <span class="line-sub">Premier Retreats</span>
      </span>
    </header>

    <section class="person">
      <h1 class="person-name"><span class="first">Marena</span> Kovalova</h1>
      <p class="person-title">Co-Founder</p>
    </section>
    <div class="accent-bar"></div>

    <ul class="contacts">
      <li>(555) 214-0387
        <svg viewBox="0 0 24 24" aria-hidden="true"><path fill="var(--brand-orange)" d="M6.6 2.5l3 3.4-1.8 2.6c1.2 2.7 3.2 4.7 5.9 6l2.6-1.8 3.4 3-1.6 3.3C10.5 19 4.9 13.4 4 4.2z"/><path d="M14 3a7 7 0 0 1 7 7M14 6.5a3.5 3.5 0 0 1 3.5 3.5" stroke="var(--brand-orange)" stroke-width="1.8" fill="none" stroke-linecap="round"/></svg>
      </li>
      <li>(555) 630-4419
        <svg viewBox="0 0 24 24" aria-hidden="true"><rect x="6.5" y="2" width="11" height="20" rx="2" fill="none" stroke="var(--brand-orange)" stroke-width="1.8"/><line x1="10.5" y1="18.5" x2="13.5" y2="18.5" stroke="var(--brand-orange)" stroke-width="1.6"/></svg>
      </li>
      <li>www.coastlinepremierretreats.example
        <svg viewBox="0 0 24 24" aria-hidden="true"><circle cx="12" cy="12" r="10" fill="var(--brand-orange)"/><path d="M2 12h20M12 2c3 3 3 17 0 20M12 2c-3 3-3 17 0 20" stroke="var(--card-bg)" stroke-width="1.4" fill="none"/></svg>
      </li>
      <li>info@coastlinepremierretreats.example
        <svg viewBox="0 0 24 24" aria-hidden="true"><path d="M2 9l10-7 10 7v12H2z" fill="var(--brand-orange)"/><path d="M2 9l10 7 10-7" stroke="var(--card-bg)" stroke-width="1.4" fill="none"/><circle cx="12" cy="8.5" r="2.4" fill="none" stroke="var(--card-bg)" stroke-width="1.2"/></svg>
      </li>
    </ul>
  </article>
</body>
</html>
```